BOLD & MINIMALIST DESIGN NEEDED

We want a very bold but minimalistic business card design that is impactful and utilizes both sides of the business card. Our current logo is included for your use.

We want bold fonts and good use of negative space. We don't want the logo to overpower the design.

Target Market(s)

Professionals who are building new commercial buildings.

Industry/Entity Type

Construction

Contact Information for Business Card

Name, Title, email, office phone, cell phone, website

Font styles to use
Serif
Sans Serif

Requirements
Must have
• Bold design!

```html
<!DOCTYPE html>
<html lang="en">
<head>
<meta charset="utf-8">
<title>Ridgeline Design + Build – Business Card</title>
<link rel="stylesheet" href="https://fonts.googleapis.com/css2?family=Montserrat:wght@500;800&family=Arimo:wght@400;700&display=swap">
<style>
  :root {
    --page-bg: #ecebe8;
    --green-deep: #0d3a03;
    --green-mid: #2f7414;
    --green-bright: #6cb33a;
    --green-accent: #79c043;
    --ink: #111111;
    --ink-soft: #4a4a4a;
    --paper: #ffffff;
    --paper-shade: #e4e4e4;
    --rule: #8a8a8a;
  }
  * { box-sizing: border-box; margin: 0; padding: 0; }
  html, body { width: 1200px; height: 900px; overflow: hidden; }
  body {
    background: var(--page-bg);
    position: relative;
    font-family: "Arimo", Arial, sans-serif;
  }
  .card {
    position: absolute;
    width: 560px;
    height: 320px;
    border-radius: 34px;
    overflow: hidden;
    box-shadow: 0 14px 30px rgba(0,0,0,.22);
  }

  /* ---------- front ---------- */
  .card-front {
    left: 150px; top: 80px;
    background: linear-gradient(225deg, var(--green-deep) 0%, var(--green-mid) 55%, var(--green-bright) 100%);
    color: var(--paper);
  }
  .card-front .swoosh { position: absolute; left: 0; bottom: 0; width: 560px; height: 120px; }
  .front-brand {
    position: absolute; right: 40px; top: 42px;
    text-align: center;
  }
  .brand-name {
    font-family: "Montserrat", sans-serif;
    font-weight: 800;
    font-size: 46px;
    letter-spacing: 1px;
    line-height: 1;
  }
  .brand-tag {
    font-family: "Montserrat", sans-serif;
    font-weight: 800;
    font-size: 13px;
    letter-spacing: 7px;
    margin-top: 6px;
    padding-top: 5px;
    border-top: 2px solid currentColor;
  }
  .services {
    position: absolute; right: 62px; top: 148px;
    text-align: center;
    font-size: 15px;
    line-height: 1.55;
  }
  .services-title {
    font-family: "Arimo", sans-serif;
    font-weight: 700;
    color: var(--green-accent);
    font-size: 15px;
    letter-spacing: .5px;
    margin-bottom: 4px;
  }

  /* ---------- back ---------- */
  .card-back {
    left: 490px; top: 500px;
    background: linear-gradient(160deg, var(--paper) 40%, #f1f1f1 100%);
    color: var(--ink);
  }
  .card-back .swoosh { position: absolute; left: 0; bottom: 0; width: 560px; height: 110px; }
  .contact {
    position: absolute; left: 38px; top: 42px;
  }
  .person-name {
    font-family: "Montserrat", sans-serif;
    font-weight: 800;
    font-size: 21px;
  }
  .person-title {
    font-size: 15px;
    color: var(--ink-soft);
    margin-bottom: 12px;
  }
  .contact-list { list-style: none; }
  .contact-list li {
    display: flex; align-items: center; gap: 9px;
    font-size: 14px; color: #2a2a2a;
    line-height: 1.6;
  }
  .contact-list svg { width: 15px; height: 15px; flex: none; }
  .contact-rule {
    width: 230px; height: 1px; background: var(--rule);
    margin: 9px 0 8px;
  }
  .address { font-size: 14px; color: #2a2a2a; line-height: 1.45; }
  .back-brand {
    position: absolute; right: 36px; top: 128px;
    display: flex; align-items: center; gap: 12px;
    color: var(--ink);
  }
  .brand-mark {
    width: 26px; height: 26px; background: var(--green-accent);
  }
  .back-brand .brand-name { font-size: 34px; }
  .back-brand .brand-tag { font-size: 10px; letter-spacing: 5px; }
</style>
</head>
<body>

<section class="card card-front" aria-label="Card front">
  <svg class="swoosh" viewBox="0 0 560 120" preserveAspectRatio="none" aria-hidden="true">
    <path d="M0 120 L0 95 Q250 40 560 10 L560 120 Z" fill="rgba(0,0,0,.18)"/>
    <path d="M0 120 L0 105 Q260 52 560 22 L560 120 Z" fill="rgba(110,180,60,.35)"/>
  </svg>
  <div class="front-brand">
    <div class="brand-name">RIDGELINE</div>
    <div class="brand-tag">DESIGN + BUILD</div>
  </div>
  <div class="services">
    <div class="services-title">SERVICES</div>
    <div>Preconstruction Planning</div>
    <div>Design / Build</div>
    <div>Construction Management</div>
  </div>
</section>

<section class="card card-back" aria-label="Card back">
  <svg class="swoosh" viewBox="0 0 560 110" preserveAspectRatio="none" aria-hidden="true">
    <path d="M0 110 L0 80 Q300 40 560 0 L560 110 Z" fill="var(--paper-shade)"/>
    <path d="M0 110 L0 92 Q300 52 560 14 L560 110 Z" fill="var(--paper)"/>
  </svg>
  <div class="contact">
    <div class="person-name">Dana Whitfield</div>
    <div class="person-title">Founder</div>
    <ul class="contact-list">
      <li>
        <svg viewBox="0 0 16 16" aria-hidden="true"><rect x="4" y="1" width="8" height="14" rx="1.5" fill="none" stroke="#79c043" stroke-width="1.5"/><line x1="7" y1="12.5" x2="9" y2="12.5" stroke="#79c043" stroke-width="1.5"/></svg>
        3XX-2XX-9XXX
      </li>
      <li>
        <svg viewBox="0 0 16 16" aria-hidden="true"><path d="M3 2 L6 2 L7 5 L5.5 6.5 Q7 9.5 9.5 10.5 L11 9 L14 10 L14 13 Q8 14 3.5 9 Q1.5 6 3 2 Z" fill="#79c043"/></svg>
        555-014-2200
      </li>
      <li>
        <svg viewBox="0 0 16 16" aria-hidden="true"><rect x="1" y="3" width="14" height="10" fill="#79c043"/><path d="M1 3 L8 9 L15 3" fill="none" stroke="#fff" stroke-width="1.3"/></svg>
        info@rdb-build.com
      </li>
      <li>
        <svg viewBox="0 0 16 16" aria-hidden="true"><circle cx="8" cy="8" r="6.5" fill="none" stroke="#79c043" stroke-width="1.3"/><ellipse cx="8" cy="8" rx="3" ry="6.5" fill="none" stroke="#79c043" stroke-width="1.1"/><line x1="1.5" y1="8" x2="14.5" y2="8" stroke="#79c043" stroke-width="1.1"/></svg>
        www.rdb-build.com
      </li>
    </ul>
    <div class="contact-rule"></div>
    <div class="address">1420 Cedar Hollow Rd.<br>Pine Ridge, GA 30000</div>
  </div>
  <div class="back-brand">
    <span class="brand-mark" aria-hidden="true"></span>
    <div>
      <div class="brand-name">RIDGELINE</div>
      <div class="brand-tag">DESIGN + BUILD</div>
    </div>
  </div>
</section>

</body>
</html>
```